Holistic/ Sports Psychologist needs flyer design

I need a flyer designed that catches the attention of potential customers - (parents of young athletes and athletes) who may be looking for psychological services. I have a logo and all the relevant info for the flyer but would like someone to take it and make it look creative, fun, fresh and attention getting for high school and college athletes. The colors used can be from my logo design which represents my holistic approach.
Target Market(s)
high school and collegiate athletes
Industry/Entity Type
sports psychology
Requirements
Must have
- Info I put on the flyer with my logo and please add some graphics and color based on my logo

```html
<!DOCTYPE html>
<html lang="en">
<head>
<meta charset="utf-8">
<title>Holistic and Sports Psychology Consulting – Flyer</title>
<link href="https://fonts.googleapis.com/css2?family=Cormorant+Garamond:wght@500;600;700&family=Great+Vibes&family=Outfit:wght@300;400;500;600&display=swap" rel="stylesheet">
<style>
  :root{
    --stage:#8eacd6;
    --paper:#ffffff;
    --forest:#3f5e3a;
    --leaf:#a9c86b;
    --lime:#b2d57c;
    --sky:#92c4e4;
    --sky-soft:#9cc6e2;
    --navy:#2e5a8a;
    --butter:#ece59c;
    --moss:#536f4a;
    --ocean:#396a9c;
    --ink:#262626;
    --body:#555a5f;
    --tag-line:#b9d99c;
    --check:#3f6b4a;
    --mark:#dcebf5;
  }
  *{margin:0;padding:0;box-sizing:border-box}
  html,body{width:1200px;height:885px;overflow:hidden;background:var(--stage)}
  .canvas{position:relative;width:1200px;height:885px;background:var(--stage)}
  .page{position:absolute;top:71px;width:527px;height:745px;background:var(--paper);overflow:hidden}
  .page--front{left:64px}
  .page--back{left:610px}
  .abs{position:absolute}
  .serif{font-family:"Cormorant Garamond",Georgia,serif;font-weight:700;line-height:.9}
  .script{font-family:"Great Vibes",cursive}
  .sans{font-family:"Outfit",Arial,sans-serif}

  /* front title */
  .title-holistic{left:35px;top:44px;font-size:46px;color:var(--forest)}
  .title-psych{left:35px;top:86px;font-size:56px;color:var(--leaf)}
  .title-and{left:35px;top:125px;font-size:28px;color:var(--forest)}
  .title-box{left:78px;top:146px;width:236px;height:99px;border:1px solid #b6d2ea;border-radius:6px;
    background:linear-gradient(160deg,#f4f8fc 0%,#fbfbf0 100%)}
  .title-sports{left:92px;top:156px;font-size:40px;color:var(--navy);line-height:.95}
  .title-consulting{left:32px;top:226px;font-size:58px;color:var(--sky-soft);line-height:1}

  .brand{left:362px;top:30px;width:144px;text-align:center}
  .brand-mark{width:84px;height:84px;margin:0 auto 6px;border-radius:50%;background:var(--mark)}
  .brand-name{font-size:13px;color:var(--navy);font-weight:400;white-space:nowrap}
  .brand-bar{height:10px;background:var(--lime);margin-top:3px}

  .photo-girl{left:284px;top:164px;width:221px;height:220px;border-radius:110px 110px 0 0;
    background:linear-gradient(180deg,#f4e2cf 0%,#e9c6a6 50%,#3d86cf 80%,#2f74bd 100%)}
  .ball-tennis{border-radius:50%;background:radial-gradient(circle at 35% 35%,#e8f56a,#b9d62a 70%,#96b21c)}
  .ball-basket{border-radius:50%;background:radial-gradient(circle at 35% 35%,#ff9a3c,#ec6a12 70%,#c24d08)}
  .racket{left:440px;top:539px;width:66px;height:206px;border-radius:50% 50% 8px 8px / 35% 35% 8px 8px;
    background:linear-gradient(180deg,#e5e5e5 0%,#d7d7d7 60%,#d08a3a 62%,#e9d3aa 100%);z-index:0}
  .butterfly{background:linear-gradient(160deg,#8fb3e6,#b6a4df);border-radius:60% 10% 60% 40%}

  .tagline{left:35px;top:319px;font-size:15px;line-height:18.5px;color:var(--ink);font-weight:400;letter-spacing:-.1px}

  .card{position:absolute;border-radius:8px;padding:10px 12px;z-index:1}
  .card h3{font-family:"Cormorant Garamond",Georgia,serif;font-weight:700;font-size:18px;line-height:.85;margin:4px 0 6px}
  .card p{font-family:"Outfit",Arial,sans-serif;font-weight:300;font-size:10.2px;line-height:12.8px}
  .card svg{display:block}
  .card--skills{left:26px;top:384px;width:147px;height:139px;background:var(--butter);color:#3d4a33}
  .card--perf{left:185px;top:384px;width:157px;height:139px;background:var(--lime);color:#3b4a30}
  .card--health{left:355px;top:384px;width:146px;height:139px;background:var(--sky);color:#2f4b63}
  .card--health h3{margin-top:14px;margin-bottom:10px}
  .card--injury{left:85px;top:537px;width:170px;height:184px;background:var(--moss);color:#fff;padding:14px 13px}
  .card--burnout{left:268px;top:537px;width:169px;height:184px;background:var(--ocean);color:#fff;padding:14px 13px}
  .card--injury h3,.card--burnout h3{margin:10px 0 8px}
  .ball-tennis,.ball-basket{z-index:2}

  /* back */
  .banner{left:29px;top:28px;width:467px;height:118px;border-radius:10px;
    background:linear-gradient(90deg,#5f9a4b 0%,#4f8a6a 45%,#3f7aa6 100%);display:flex;align-items:center;justify-content:center}
  .banner h2{font-family:"Cormorant Garamond",Georgia,serif;font-weight:600;font-size:44px;color:#fff}
  .photo-runner{left:262px;top:154px;width:265px;height:257px;
    background:linear-gradient(180deg,#ffffff 0%,#f1f3f5 40%,#cfd4d9 100%)}
  .bio{left:29px;top:168px;width:230px;font-size:13.4px;line-height:17px;color:var(--body);font-weight:300;white-space:nowrap}
  .spec-her{left:29px;top:346px;font-size:21px;color:var(--navy);font-weight:600}
  .spec-title{left:29px;top:366px;font-size:23px;color:var(--navy);font-weight:600}
  .spec-include{left:29px;top:386px;font-size:26px;color:var(--forest)}

  .tag{position:absolute;height:36px;border:1px solid var(--tag-line);background:#fff;
    font-family:"Outfit",Arial,sans-serif;font-size:13.4px;color:var(--ink);display:flex;align-items:center;justify-content:center;white-space:nowrap}
  .tag .tick{position:absolute;left:-8px;top:-5px}
  .telehealth{left:29px;top:612px;font-size:15px;line-height:19.5px;font-weight:600;color:#6a9a45}
  .telehealth span{color:var(--navy)}
  .sessions{left:29px;top:660px;width:231px;height:41px;background:var(--lime);border-radius:3px;
    display:flex;align-items:center;justify-content:center;font-size:15px;font-weight:500;color:#2c3b24}
  .reach{left:314px;top:578px;font-size:30px;color:var(--navy);font-weight:600}
  .contact{left:314px;font-size:13.5px;font-weight:500;color:var(--ink);display:flex;gap:10px;line-height:15.5px}
  .contact svg{flex:none;margin-top:1px}
</style>
</head>
<body>
<div class="canvas">

  <section class="page page--front">
    <div class="abs serif title-holistic">Holistic</div>
    <div class="abs serif title-psych">Psychology</div>
    <div class="abs script title-and">and</div>
    <div class="abs title-box"></div>
    <div class="abs serif title-sports">Sports<br>Psychology</div>
    <div class="abs script title-consulting">Consulting</div>

    <div class="abs butterfly" role="img" aria-label="Butterfly illustration" style="left:296px;top:128px;width:38px;height:52px"></div>
    <div class="abs butterfly" role="img" aria-label="Small butterfly illustration" style="left:35px;top:222px;width:16px;height:22px"></div>

    <div class="abs brand sans">
      <div class="brand-mark"></div>
      <div class="brand-name">Dr. Elena Whitcombe</div>
      <div class="brand-bar"></div>
    </div>

    <div class="abs photo-girl" role="img" aria-label="Photo of a smiling young girl holding a basketball and giving a thumbs up"></div>

    <p class="abs sans tagline">Ways to Improve Athletic Performance<br>Using Sports and Holistic Psychology.</p>

    <div class="card card--skills">
      <svg width="20" height="20" viewBox="0 0 20 20" aria-hidden="true"><path d="M5 18v-4c-2-1-3-3-3-6a7 7 0 0 1 14 0l1 4h-2v3h-3v3z" fill="#3f5e3a"/></svg>
      <h3>Mental Skills<br>Training</h3>
      <p>Ex Visualization, goal-setting, motivation, self- talk, mindset, concentration techniques.</p>
    </div>
    <div class="card card--perf">
      <svg width="22" height="20" viewBox="0 0 22 20" aria-hidden="true"><circle cx="11" cy="13" r="5" fill="none" stroke="#3f5e3a" stroke-width="3" stroke-dasharray="3 2"/><circle cx="11" cy="13" r="2" fill="#3f5e3a"/><path d="M5 3l1 2M11 1v3M17 3l-1 2" stroke="#3f5e3a" stroke-width="2"/></svg>
      <h3>Performance<br>Enhancement</h3>
      <p>Eliminate psychological barriers that are hindering performance such as self-doubt, perfectionism, fear of failure, and burnout.</p>
    </div>
    <div class="card card--health">
      <svg width="20" height="18" viewBox="0 0 20 18" aria-hidden="true"><path d="M10 17 2 9a4.5 4.5 0 0 1 8-5 4.5 4.5 0 0 1 8 5z" fill="#2e5a8a"/></svg>
      <h3>Mental Health</h3>
      <p>Anxiety and stress management by using relaxation techniques, breathwork, and mindfulness practices.</p>
    </div>
    <div class="card card--injury">
      <svg width="20" height="18" viewBox="0 0 20 18" aria-hidden="true"><path d="M10 17 2 9a4.5 4.5 0 0 1 8-5 4.5 4.5 0 0 1 8 5z" fill="#fff"/></svg>
      <h3>Injury Recovery<br>Support</h3>
      <p>Assist athletes in maintaining resilience and positive mental attitude during rehabilitation as well as processing emotions relating to any potential trauma caused by the injury or life transitions resulting from it.</p>
    </div>
    <div class="card card--burnout">
      <svg width="20" height="22" viewBox="0 0 20 22" aria-hidden="true"><circle cx="12" cy="4" r="2.5" fill="#fff"/><path d="M11 8l-3 6 4 2-2 5M8 14l-4 3M11 8l4 3" stroke="#fff" stroke-width="2" fill="none"/></svg>
      <h3>Burnout<br>prevention</h3>
      <p>teach athletes how to have balance in sports and life so they can experience longevity in their sports as well as overall optimal health and well-being.</p>
    </div>

    <div class="abs ball-tennis" role="img" aria-label="Tennis ball" style="left:131px;top:357px;width:40px;height:40px"></div>
    <div class="abs ball-basket" role="img" aria-label="Basketball" style="left:13px;top:630px;width:80px;height:80px"></div>
    <div class="abs racket" role="img" aria-label="Tennis racket"></div>
  </section>

  <section class="page page--back">
    <div class="abs banner" role="img" aria-label="Photo of runners' legs on a track, tinted green and blue">
      <h2>Background</h2>
    </div>
    <div class="abs photo-runner" role="img" aria-label="Photo of a young sprinter crouched in the starting position"></div>

    <p class="abs sans bio">Dr. Elena Whitcombe is a<br>licensed psychologist. She<br>understands the unique experiences<br>of athletes due to her background as<br>an All-American swimmer, collegiate<br>and age group swim coach, parent<br>of a collegiate/professional athlete,<br>and sports psychology researcher.<br>She works with athletes to optimize<br>performance and overall well-being.</p>

    <div class="abs serif spec-her">Her</div>
    <div class="abs serif spec-title">Specializations</div>
    <div class="abs script spec-include">Include</div>

    <div class="tag" style="left:34px;top:426px;width:106px"><svg class="tick" width="18" height="18" viewBox="0 0 18 18"><path d="M2 10l5 5L16 2" stroke="var(--navy)" stroke-width="3" fill="none"/></svg>Anxiety</div>
    <div class="tag" style="left:152px;top:426px;width:106px"><svg class="tick" width="18" height="18" viewBox="0 0 18 18"><path d="M2 10l5 5L16 2" stroke="var(--check)" stroke-width="3" fill="none"/></svg>Depressions</div>
    <div class="tag" style="left:268px;top:426px;width:106px"><svg class="tick" width="18" height="18" viewBox="0 0 18 18"><path d="M2 10l5 5L16 2" stroke="var(--navy)" stroke-width="3" fill="none"/></svg>Trauma</div>
    <div class="tag" style="left:385px;top:426px;width:106px"><svg class="tick" width="18" height="18" viewBox="0 0 18 18"><path d="M2 10l5 5L16 2" stroke="var(--check)" stroke-width="3" fill="none"/></svg>Injury &amp; Sleep.</div>

    <div class="tag" style="left:34px;top:473px;width:149px"><svg class="tick" width="18" height="18" viewBox="0 0 18 18"><path d="M2 10l5 5L16 2" stroke="var(--check)" stroke-width="3" fill="none"/></svg>Performance Anxiety</div>
    <div class="tag" style="left:197px;top:473px;width:148px"><svg class="tick" width="18" height="18" viewBox="0 0 18 18"><path d="M2 10l5 5L16 2" stroke="var(--navy)" stroke-width="3" fill="none"/></svg>Stress Management</div>
    <div class="tag" style="left:355px;top:473px;width:136px"><svg class="tick" width="18" height="18" viewBox="0 0 18 18"><path d="M2 10l5 5L16 2" stroke="var(--check)" stroke-width="3" fill="none"/></svg>Relationship Issues</div>

    <div class="tag" style="left:34px;top:521px;width:106px"><svg class="tick" width="18" height="18" viewBox="0 0 18 18"><path d="M2 10l5 5L16 2" stroke="var(--navy)" stroke-width="3" fill="none"/></svg>Life Transitions</div>
    <div class="tag" style="left:154px;top:521px;width:148px"><svg class="tick" width="18" height="18" viewBox="0 0 18 18"><path d="M2 10l5 5L16 2" stroke="var(--check)" stroke-width="3" fill="none"/></svg>Mental Performance</div>

    <div class="abs ball-tennis" role="img" aria-label="Tennis ball" style="left:424px;top:505px;width:67px;height:67px"></div>
    <div class="abs butterfly" role="img" aria-label="Butterfly illustration" style="left:212px;top:589px;width:36px;height:48px"></div>

    <p class="abs sans telehealth">All services are provided<br><span>online via Telehealth.</span></p>
    <div class="abs sans sessions">Sessions are 30 or 55 minutes</div>

    <div class="abs serif reach">Reach Us!</div>
    <svg class="abs" style="left:466px;top:592px" width="14" height="42" viewBox="0 0 14 42" aria-hidden="true"><path d="M4 1c8 10 8 24 2 38M1 32l5 7 6-5" stroke="var(--forest)" stroke-width="1.4" fill="none"/></svg>

    <div class="abs sans contact" style="top:632px">
      <svg width="14" height="14" viewBox="0 0 14 14"><path d="M3 1l2.5 3-1.5 2a8 8 0 0 0 4 4l2-1.5 3 2.5-1.5 2C6 13 1 8 1 2.5z" fill="#8cc06a"/></svg>
      <span>555-014-2290</span>
    </div>
    <div class="abs sans contact" style="top:652px">
      <svg width="14" height="14" viewBox="0 0 14 14"><path d="M2 1l10 5-4 1.5L6 12z" fill="#8fb8e0"/></svg>
      <span>drelenawhitcombe.com</span>
    </div>
    <div class="abs sans contact" style="top:672px">
      <svg width="14" height="16" viewBox="0 0 14 16"><path d="M7 15S1 9 1 6a6 6 0 0 1 12 0c0 3-6 9-6 9z" fill="#8cc06a"/><circle cx="7" cy="6" r="2.2" fill="#fff"/></svg>
      <span>2280 Harbor Lane #105<br>Seabrook, FL<br>32000.</span>
    </div>
  </section>

</div>
</body>
</html>
```